Moravel Aesthetic Doctor

I require an elegant, luxurious looking business card for my aesthetic business. I am a doctor and that will set me aside from competitors. I am planning to provide home and spa based treatments to clients with high expectations. I have attached my logo.

```html
<!DOCTYPE html>
<html lang="en">
<head>
<meta charset="utf-8">
<title>Moravel Aesthetic Doctor — Business Card</title>
<link rel="stylesheet" href="https://fonts.googleapis.com/css2?family=Marcellus&family=Arimo:wght@400;700&display=swap">
<style>
  :root {
    --stage: #9a9a9c;
    --card-white: #ffffff;
    --blue-deep: #1a7fd0;
    --blue-mid: #2e93da;
    --blue-light: #62b6e6;
    --band: #7dcbee;
    --accent: #5bbbe8;
    --grey-text: #7b7b80;
    --grey-name: #a2a2a6;
    --rule: #9a9a9e;
  }
  * { box-sizing: border-box; margin: 0; padding: 0; }
  html, body { width: 1200px; height: 1200px; overflow: hidden; }
  body {
    background: var(--stage);
    position: relative;
    font-family: "Arimo", Arial, sans-serif;
  }
  .card {
    position: absolute;
    top: 305px;
    height: 591px;
    border-radius: 14px;
    overflow: hidden;
    text-align: center;
  }
  .card--front { left: 201px; width: 367px; }
  .card--back { left: 600px; width: 362px; background: var(--card-white); }

  .front-backdrop {
    position: absolute; inset: 0;
    background: linear-gradient(160deg, var(--blue-light) 0%, var(--blue-mid) 18%, var(--blue-deep) 38%, var(--blue-mid) 62%, var(--blue-deep) 76%, var(--blue-light) 100%);
  }
  .front-brand {
    position: absolute; top: 118px; left: 0; right: 0;
    font-family: "Marcellus", serif;
    color: #fff;
  }
  .front-brand__name { font-size: 58px; letter-spacing: 3px; line-height: 1; }
  .front-brand__sub { font-size: 24px; letter-spacing: 1px; margin-top: 8px; }

  .services {
    position: absolute; top: 330px; left: 0; right: 0;
    list-style: none; color: #fff;
    font-size: 18px; line-height: 29.2px;
  }
  .service-band {
    position: absolute; top: 493px; left: 0; right: 0; height: 52px;
    background: var(--band); color: #fff;
    font-size: 17.5px; line-height: 52px;
  }

  .back-brand {
    position: absolute; top: 118px; left: 0; right: 0;
    display: flex; align-items: center; justify-content: center; gap: 14px;
  }
  .back-brand__dot {
    width: 62px; height: 62px; border-radius: 50%;
    background: var(--accent); flex: none;
  }
  .back-brand__name {
    font-family: "Marcellus", serif; color: var(--grey-name);
    text-align: left; line-height: 1.05;
  }
  .back-brand__name .big { display: block; font-size: 38px; letter-spacing: 2px; }
  .back-brand__name .small { display: block; font-size: 17px; letter-spacing: 1px; }

  .doctor { position: absolute; top: 322px; left: 0; right: 0; }
  .doctor__name { font-size: 24px; font-weight: 700; color: var(--grey-name); }
  .doctor__post { font-size: 15px; font-weight: 400; color: var(--accent); }
  .doctor__diploma { font-size: 17px; color: var(--accent); line-height: 21px; margin-top: 4px; }

  .divider {
    position: absolute; left: 0; right: 0;
    display: flex; align-items: center; justify-content: center; gap: 4px;
  }
  .divider__line { width: 52px; height: 1px; background: var(--rule); margin: 0 4px; }
  .divider--icons { top: 410px; }
  .divider--social { top: 526px; }
  .icon-tile {
    width: 25px; height: 25px; border-radius: 3px; background: var(--band);
    display: flex; align-items: center; justify-content: center;
  }
  .social-dot { width: 28px; height: 28px; border-radius: 50%; background: var(--accent); margin: 0 2px; }

  .contact {
    position: absolute; top: 448px; left: 0; right: 0;
    font-size: 17px; line-height: 21.5px; color: var(--grey-text);
  }
</style>
</head>
<body>
  <section class="card card--front">
    <div class="front-backdrop" role="img" aria-label="Flowing blue wave background"></div>
    <div class="front-brand">
      <div class="front-brand__name">MORAVEL</div>
      <div class="front-brand__sub">AESTHETIC DOCTOR</div>
    </div>
    <ul class="services">
      <li>DERMAL INJECTABLES</li>
      <li>PLASMA FACIALS</li>
      <li>MICRONEEDLING</li>
      <li>SKIN BOOSTERS</li>
      <li>EXCESSIVE SWEATING</li>
    </ul>
    <div class="service-band">HOME AND SPA BASED TREATMENTS</div>
  </section>

  <section class="card card--back">
    <div class="back-brand">
      <span class="back-brand__dot"></span>
      <div class="back-brand__name">
        <span class="big">MORAVEL</span>
        <span class="small">AESTHETIC DOCTOR</span>
      </div>
    </div>

    <div class="doctor">
      <div class="doctor__name">Dr Elise Varden <span class="doctor__post">MRCPCH MD</span></div>
      <div class="doctor__diploma">Australasian Diploma of<br>Aesthetic Medicine</div>
    </div>

    <div class="divider divider--icons">
      <span class="divider__line"></span>
      <span class="icon-tile">
        <svg width="16" height="14" viewBox="0 0 16 14" aria-hidden="true"><path d="M1 5 Q8 0 15 5 L13 7 L11 5 L5 5 L3 7 Z M4 7 H12 L13 13 H3 Z" fill="#fff"/></svg>
      </span>
      <span class="icon-tile">
        <svg width="16" height="12" viewBox="0 0 16 12" aria-hidden="true"><rect x="1" y="1" width="14" height="10" fill="none" stroke="#fff" stroke-width="1.4"/><path d="M1 1 L8 7 L15 1" fill="none" stroke="#fff" stroke-width="1.4"/></svg>
      </span>
      <span class="icon-tile">
        <svg width="16" height="16" viewBox="0 0 16 16" aria-hidden="true"><circle cx="8" cy="8" r="6.5" fill="none" stroke="#fff" stroke-width="1.4"/><path d="M1.5 8 H14.5 M8 1.5 Q4 8 8 14.5 M8 1.5 Q12 8 8 14.5" fill="none" stroke="#fff" stroke-width="1.2"/></svg>
      </span>
      <span class="divider__line"></span>
    </div>

    <div class="contact">
      <div>0800 345 718</div>
      <div>elise@moravel.co.nz</div>
      <div>www.moravel.co.nz</div>
    </div>

    <div class="divider divider--social">
      <span class="divider__line" style="width:58px"></span>
      <span class="social-dot"></span>
      <span class="social-dot"></span>
      <span class="divider__line" style="width:66px"></span>
    </div>
  </section>
</body>
</html>
```